Maple Roster Business Card for recruitment company

We are looking for a Business Card Design that incorporates our personal details and our busines name and logo. We are a specialized search consultancy that recruit Property and Construction professionals.
We would like a business card that stands out and is appealing to the Construction and Property industry as well.

Target Market(s)

people in the construction and property industry

Contact Information for Business Card

Business Name and logo

Font styles to use
Serif

Colors
0094D4
00A9DD
6FCCEA
C7EBF8
E9F6FB

Requirements
Must have
• Business name and logo as well as contact details
Should not have
• No photos of us please

```html
<!DOCTYPE html>
<html lang="en">
<head>
<meta charset="utf-8">
<title>Maple Roster — Business Card</title>
<link rel="stylesheet" href="https://fonts.googleapis.com/css2?family=Source+Serif+4:opsz,wght@8..60,400;8..60,700&display=swap">
<style>
  :root {
    --backdrop: #c8c8c8;
    --blue-strong: #0094d4;
    --blue-bright: #00a9dd;
    --blue-soft: #6fccea;
    --blue-pale: #c7ebf8;
    --blue-mist: #e9f6fb;
    --ink: #0b4f6e;
    --text-body: #3f5560;
    --text-muted: #5f7480;
    --white: #ffffff;
  }
  * { margin: 0; padding: 0; box-sizing: border-box; }
  html, body {
    width: 1200px;
    height: 1000px;
    overflow: hidden;
    background: var(--backdrop);
    font-family: "Source Serif 4", serif;
  }
  .canvas { position: relative; width: 1200px; height: 1000px; }

  .card { position: absolute; width: 625px; height: 375px; overflow: hidden; }

  /* Front */
  .card--front { left: 94px; top: 105px; background: var(--blue-strong); }
  .front-pattern {
    position: absolute; inset: 0;
    background: linear-gradient(135deg, var(--blue-strong) 0%, var(--blue-bright) 100%);
  }
  .front-mark {
    position: absolute; right: 52px; top: 268px;
    display: flex; align-items: center; gap: 8px;
    color: var(--white);
    font-size: 16px; font-weight: 400; letter-spacing: 2px; text-transform: uppercase;
    line-height: 1;
  }
  .front-mark__dot {
    width: 12px; height: 12px; border-radius: 50%; background: var(--white); flex: none;
  }

  /* Back */
  .card--back { left: 474px; top: 509px; background: var(--blue-mist); }
  .back-band {
    position: absolute; left: 0; right: 0; bottom: 0; height: 6px;
    background: linear-gradient(90deg, var(--blue-strong), var(--blue-bright), var(--blue-soft));
  }
  .wordmark {
    position: absolute; left: 35px; top: 134px;
    color: var(--blue-strong);
    font-size: 27px; font-weight: 400; letter-spacing: 1.5px; text-transform: uppercase;
    line-height: 1;
  }
  .contact { position: absolute; left: 364px; top: 128px; color: var(--ink); }
  .contact__name {
    font-size: 24px; font-weight: 700; line-height: 1.1; color: var(--blue-strong);
  }
  .contact__role { font-size: 12.5px; color: var(--text-muted); margin-top: 3px; line-height: 1.3; }
  .contact__list { list-style: none; margin-top: 22px; }
  .contact__item {
    display: flex; align-items: center; gap: 7px;
    font-size: 15.5px; color: var(--text-body); line-height: 24px;
  }
  .contact__item svg { width: 13px; height: 13px; fill: var(--blue-strong); flex: none; }
  .contact__web {
    position: absolute; left: 364px; top: 309px;
    font-size: 15.5px; color: var(--blue-strong); line-height: 1.2;
  }
</style>
</head>
<body>
<main class="canvas">
  <section class="card card--front" aria-label="Card front">
    <div class="front-pattern" role="img" aria-label="Repeating tonal brand pattern across the card face"></div>
    <div class="front-mark"><span class="front-mark__dot"></span>Maple Roster</div>
  </section>

  <section class="card card--back" aria-label="Card back">
    <div class="wordmark">Maple Roster</div>

    <div class="contact">
      <h1 class="contact__name">Harriet Coleman</h1>
      <p class="contact__role">Director | Senior Search Consultant</p>
      <ul class="contact__list">
        <li class="contact__item">
          <svg viewBox="0 0 24 24" aria-hidden="true"><path d="M6.6 10.8a15.1 15.1 0 0 0 6.6 6.6l2.2-2.2a1 1 0 0 1 1-.25 11.4 11.4 0 0 0 3.6.57 1 1 0 0 1 1 1V20a1 1 0 0 1-1 1A17 17 0 0 1 3 4a1 1 0 0 1 1-1h3.5a1 1 0 0 1 1 1c0 1.25.2 2.45.57 3.57a1 1 0 0 1-.25 1z"/></svg>
          +64 21 555 0142
        </li>
        <li class="contact__item">
          <svg viewBox="0 0 24 24" aria-hidden="true"><path d="M2 5h20v14H2V5zm2 2.2V17h16V7.2l-8 6.3-8-6.3zM5.2 7 12 12.3 18.8 7H5.2z"/></svg>
          hello@mapleroster.co
        </li>
      </ul>
    </div>

    <div class="contact__web">mapleroster.nz</div>
    <div class="back-band"></div>
  </section>
</main>
</body>
</html>
```